I need to have a website created  for my company , Plum Wheels.  What we are selling is mini electric trucks . These mini electric trucks require no license
or insurance.  They only go 25 k/h and are considered to be electric  mobility covered  scooters .  So far i only have a dozen of these just to see how well they sell before i sink a bunch of money into other models , designs ect. I am submitting 5 or 6 pics of the model to be put on the website along with one pic containing the specs of  the model i am going to sell .  Plum Wheels is the name of the company with our catch phrase : Cruise along on a plum wheel.  The consumers i would like to target mostly are people who are unable to get a  drivers license .  It would give seniors who have had their license taken away for medical reasons,  age etc. Anyone who does not have the luxury of having a car  but still need to do life tasks like going to grocery store ,  dr appt  but have to rely on someone else to take them . This scooter gives them that freedom to get where they want whenever they want to keep their independence at an affordable price.  The web domain i already have is at www.plumwheelsco.ca  i will also include a pic of my business cards that contains all the info of the company eg. Phone number , email etc. Thank you for you time and creativity

```html
<!DOCTYPE html>
<html lang="en">
<head>
<meta charset="utf-8">
<title>Plum Wheels – No Licence or Insurance Electric Mini Trucks</title>
<link href="https://fonts.googleapis.com/css2?family=Lato:ital,wght@0,400;0,700;0,900;1,400&family=Montserrat:wght@400;500;600&display=swap" rel="stylesheet">
<style>
:root{
  --green:#82ad21;
  --teal:#1c3f36;
  --ink:#1f1f1f;
  --section-grey:#eeeff1;
  --white:#fff;
}
*{box-sizing:border-box;margin:0;padding:0}
html,body{width:1200px;height:3261px;overflow:hidden}
body{font-family:'Lato',sans-serif;color:var(--ink);background:var(--white);position:relative}

/* header */
.site-header{position:absolute;left:0;top:0;width:1200px;height:90px;background:var(--white)}
.brand{position:absolute}
.brand-name{font-weight:900;font-size:23px;letter-spacing:.2px;color:var(--ink);line-height:1.1}
.brand-tag{font-size:15px;color:var(--ink);margin-top:4px}
.site-header .brand{left:197px;top:19px}
.main-nav{position:absolute;right:115px;top:33px;display:flex;gap:42px;font-size:15px}
.main-nav a{color:var(--ink);text-decoration:none}
.main-nav a.active{color:var(--green)}
.main-nav .login::before{content:"";display:inline-block;width:9px;height:11px;background:var(--green);border-radius:5px 5px 2px 2px;margin-right:8px;vertical-align:-1px}

/* hero */
.hero{position:absolute;left:0;top:90px;width:1200px;height:695px;overflow:hidden}
.hero-photo{position:absolute;inset:0;background:linear-gradient(110deg,#8a8f94 0%,#5e5a55 30%,#3b3d40 55%,#6d7277 80%,#9aa0a5 100%)}
.hero-tab{position:absolute;left:0;top:150px;width:51px;height:380px;background:var(--green);display:flex;align-items:center;justify-content:center}
.hero-tab span{transform:rotate(-90deg);white-space:nowrap;color:var(--white);font-weight:900;font-size:23px}
.hero-disc{position:absolute;left:611px;top:138px;width:456px;height:456px;border-radius:50%;background:rgba(35,35,35,.72)}
.hero-title{position:absolute;left:611px;top:284px;width:456px;text-align:center;color:var(--white);font-weight:900;font-size:55px;letter-spacing:-.5px;white-space:nowrap}
.hero-text{position:absolute;left:646px;top:356px;width:386px;text-align:center;color:var(--white);font-size:13px;line-height:29px}
.btn{display:flex;align-items:center;justify-content:center;background:var(--green);color:var(--white);font-weight:700;border-radius:30px;text-decoration:none}
.hero .btn{position:absolute;left:748px;top:454px;width:185px;height:45px;font-size:16px}
.slide-dots{position:absolute;left:1143px;top:262px;display:flex;flex-direction:column;align-items:center;gap:14px}
.slide-dots i{display:block;width:14px;height:14px;border:2px solid var(--white);border-radius:50%}
.slide-dots i.on{background:var(--white)}
.hero-wave{position:absolute;left:0;top:0}

/* about */
.about{position:absolute;left:0;top:785px;width:1200px;height:447px;background:var(--section-grey);text-align:center}
.section-title{font-weight:900;font-size:43px;color:var(--ink);letter-spacing:-.5px}
.about .section-title{position:absolute;left:0;width:1200px;top:50px}
.about p{position:absolute;left:172px;top:118px;width:856px;font-family:Arial,sans-serif;font-size:13.6px;line-height:28.5px;color:#444}
.about .btn{position:absolute;left:497px;top:340px;width:206px;height:52px;font-size:17px;box-shadow:0 4px 8px rgba(0,0,0,.15)}

/* benefits */
.benefits{position:absolute;left:0;top:1232px;width:1200px;height:878px;overflow:hidden}
.benefits-photo{position:absolute;inset:0;background:linear-gradient(180deg,#f3f5f4 0%,#e4e9e7 45%,#dfe3e2 70%,#eef0f0 100%)}
.benefits .section-title{position:absolute;left:0;width:1200px;top:75px;text-align:center}
.benefits .lead{position:absolute;left:350px;width:500px;top:140px;text-align:center;font-size:15px;line-height:26px;color:#333}
.benefit-ring{position:absolute;left:0;top:0}
.benefit-icon{position:absolute;width:66px;height:66px;margin:-33px 0 0 -33px;border-radius:50%;background:var(--teal);display:flex;align-items:center;justify-content:center}
.benefit-label{position:absolute;font-size:16px;line-height:26px;color:#222}
.benefit-label b{font-weight:700;display:block;text-transform:uppercase;font-size:16px}
.benefit-label.right{text-align:right}
.benefit-label.center{text-align:center;width:200px;margin-left:-100px}
.truck-photo{position:absolute;left:452px;top:401px;width:310px;height:210px;border-radius:30px;background:radial-gradient(ellipse at center,#d9dbdc 0%,#b9bcbe 55%,rgba(200,203,205,0) 75%)}

/* testimonials */
.testimonials{position:absolute;left:0;top:2110px;width:1200px;height:714px;background:var(--green)}
.testimonials .section-title{position:absolute;left:0;width:1200px;top:62px;text-align:center;color:var(--white);font-size:43px}
.quote-card{position:absolute;width:298px;height:397px;background:var(--white);box-shadow:0 8px 24px rgba(0,0,0,.08);padding:16px 20px}
.avatar{width:83px;height:83px;border-radius:50%;background:linear-gradient(160deg,#c9a58a,#6b5a50)}
.stars{position:absolute;right:32px;top:44px;display:flex;gap:3px}
.stars svg{width:11px;height:11px}
.quote-name{font-family:'Montserrat',sans-serif;font-size:13px;font-weight:500;margin:22px 0 0 10px}
.quote-text{font-style:italic;font-size:12.4px;line-height:24px;color:#777;margin:16px 0 0 10px}
.slider-arrows{position:absolute;left:536px;top:598px;display:flex;gap:9px}
.slider-arrows span{width:59px;height:59px;border-radius:50%;background:var(--white);display:flex;align-items:center;justify-content:center}

/* footer */
.site-footer{position:absolute;left:0;top:2824px;width:1200px;height:437px;font-family:'Montserrat',sans-serif}
.site-footer .brand{left:197px;top:48px;font-family:'Lato',sans-serif}
.footer-links{position:absolute;left:113px;top:143px;list-style:none;font-size:14px;line-height:37px;color:#333}
.footer-contact{position:absolute;left:279px;top:143px;list-style:none;font-size:14px;color:#333}
.footer-contact li{position:relative;padding-left:23px;line-height:37px}
.footer-contact li.addr{line-height:28px;padding-top:4px}
.footer-contact svg{position:absolute;left:0;top:13px}
.subscribe{position:absolute;left:781px;top:140px;width:310px}
.subscribe h3{font-size:17px;font-weight:600;letter-spacing:.5px;color:#222}
.subscribe p{font-size:13.5px;color:#444;margin-top:10px}
.subscribe-form{margin-top:22px;display:flex;height:53px;border:1px solid #333;border-radius:8px;overflow:hidden}
.subscribe-form span{flex:1;padding-left:11px;display:flex;align-items:center;font-size:13.5px;color:#444}
.subscribe-form b{width:128px;background:var(--teal);color:var(--white);font-weight:500;font-size:13.5px;display:flex;align-items:center;justify-content:center;border-radius:8px}
.copyright{position:absolute;left:110px;top:372px;font-size:15px;color:#333}
.social{position:absolute;left:980px;top:372px;display:flex;gap:14px}
.social span{width:18px;height:18px;border-radius:50%;background:#1f1f1f}
</style>
</head>
<body>

<header class="site-header">
  <div class="brand">
    <div class="brand-name">PLUM WHEELS</div>
    <div class="brand-tag">Cruise along on a plum wheel.</div>
  </div>
  <nav class="main-nav">
    <a class="active" href="#">Home</a>
    <a href="#">About Us</a>
    <a href="#">Products</a>
    <a href="#">Blog</a>
    <a href="#">Contact</a>
    <a class="login" href="#">Login</a>
  </nav>
</header>

<section class="hero">
  <div class="hero-photo" role="img" aria-label="Photo of a driver at the wheel of a vehicle cab"></div>
  <div class="hero-tab"><span>NO LICENSE OR INSURANCE</span></div>
  <div class="hero-disc"></div>
  <h1 class="hero-title">PLUM WHEELS</h1>
  <p class="hero-text">Lorem ipsum dolor sit amet, consectetur adipiscing elit, sed do eiusmod tempor incididunt ut labore et dolore magna aliqua. Ut enim ad minim veniam, quis nostrud exercitation</p>
  <a class="btn" href="#">Get Started</a>
  <div class="slide-dots">
    <svg width="12" height="8" viewBox="0 0 12 8"><path d="M1 7 6 2l5 5" stroke="#fff" stroke-width="2" fill="none"/></svg>
    <i></i><i></i><i class="on"></i><i></i><i></i>
    <svg width="12" height="8" viewBox="0 0 12 8"><path d="M1 1l5 5 5-5" stroke="#fff" stroke-width="2" fill="none"/></svg>
  </div>
  <svg class="hero-wave" width="1200" height="695" viewBox="0 0 1200 695">
    <path d="M0 695V650C170 590 390 585 620 630 840 672 1030 680 1200 600V695Z" fill="var(--green)"/>
    <path d="M0 695V690C180 625 390 622 620 662 840 700 1030 700 1200 612V695Z" fill="var(--section-grey)"/>
  </svg>
</section>

<section class="about">
  <h2 class="section-title">ABOUT US</h2>
  <p>Lorem ipsum dolor sit amet, consectetur adipiscing elit, sed do eiusmod tempor incididunt ut labore et dolore magna aliqua. Ut enim ad minim veniam, quis nostrud exercitation ullamco laboris nisi ut aliquip ex ea commodo consequat. Duis aute irure dolor in reprehenderit in voluptate velit esse cillum dolore eu fugiat nulla pariatur. Excepteur sint occaecat cupidatat non proident, sunt in culpa qui officia deserunt mollit anim id est laborum. Lorem ipsum dolor sit amet, consectetur adipiscing elit, sed do eiusmod tempor incididunt ut labore et dolore magna aliqua. Ut enim ad minim veniam, quis nostrud exercitation ullamco laboris nisi ut aliquip ex ea commodo consequat. Duis aute irure dolor in reprehenderit in voluptate velit esse cillum dolore eu fugiat nulla pariatur. Excepteur sint occaecat cupidatat non proident, sunt in culpa qui officia deserunt mollit anim id est laborum.</p>
  <a class="btn" href="#">Read More</a>
</section>

<section class="benefits">
  <div class="benefits-photo" role="img" aria-label="Faded photo of a truck on a road"></div>
  <h2 class="section-title">PRODUCT BENEFITS</h2>
  <p class="lead">Lorem ipsum dolor sit amet, consectetur adipiscing elit, sed do eiusmod tempor incididunt ut labore et dolore magna aliqua.</p>
  <svg class="benefit-ring" width="1200" height="878"><circle cx="600" cy="513" r="211" fill="none" stroke="#333" stroke-width="1"/></svg>
  <div class="truck-photo" role="img" aria-label="Photo of the white electric mini pickup truck"></div>

  <div class="benefit-icon" style="left:600px;top:302px"><svg width="34" height="26" viewBox="0 0 34 26" fill="none" stroke="#fff" stroke-width="2"><rect x="2" y="4" width="26" height="18" rx="4"/><path d="M30 10v6M17 7l-5 7h7l-4 6"/></svg></div>
  <div class="benefit-icon" style="left:465px;top:358px"><svg width="30" height="30" viewBox="0 0 30 30" fill="none" stroke="#fff" stroke-width="2"><path d="M15 3 27 10 15 17 3 10Z"/><path d="M3 15l12 7 12-7M3 20l12 7 12-7"/></svg></div>
  <div class="benefit-icon" style="left:748px;top:358px"><svg width="30" height="30" viewBox="0 0 30 30" fill="none" stroke="#fff" stroke-width="2"><circle cx="15" cy="15" r="12"/><circle cx="10" cy="11" r="2"/><circle cx="17" cy="9" r="2"/><path d="M14 27l12-12"/></svg></div>
  <div class="benefit-icon" style="left:401px;top:467px"><svg width="20" height="34" viewBox="0 0 20 34" fill="none" stroke="#fff" stroke-width="2"><rect x="2" y="5" width="16" height="27" rx="2"/><path d="M7 2h6M6 11h8M6 16h8M6 21h8M6 26h8"/></svg></div>
  <div class="benefit-icon" style="left:805px;top:467px"><svg width="32" height="32" viewBox="0 0 32 32" fill="none" stroke="#fff" stroke-width="2"><circle cx="16" cy="16" r="13"/><circle cx="16" cy="16" r="4"/><path d="M3 16h9M20 16h9M16 20v9"/></svg></div>
  <div class="benefit-icon" style="left:401px;top:585px"><svg width="32" height="30" viewBox="0 0 32 30" fill="none" stroke="#fff" stroke-width="2"><rect x="6" y="8" width="18" height="16" rx="2"/><path d="M10 8V4h10v4M24 13h5v6h-5M6 13H2v6h4M10 12v8M15 12v8M20 12v8"/></svg></div>
  <div class="benefit-icon" style="left:805px;top:585px"><svg width="30" height="34" viewBox="0 0 30 34" fill="none" stroke="#fff" stroke-width="2"><ellipse cx="17" cy="17" rx="11" ry="15"/><ellipse cx="17" cy="17" rx="5" ry="8"/><path d="M6 17c0-8 4-15 9-15M6 17c0 8 4 15 9 15"/></svg></div>
  <div class="benefit-icon" style="left:467px;top:685px"><svg width="32" height="26" viewBox="0 0 32 26" fill="none" stroke="#fff" stroke-width="2"><path d="M3 22a13 13 0 1 1 26 0"/><path d="M16 22l6-11"/><path d="M8 12l2 2M16 6v3M24 12l-2 2"/></svg></div>
  <div class="benefit-icon" style="left:739px;top:685px"><svg width="32" height="32" viewBox="0 0 32 32" fill="none" stroke="#fff" stroke-width="2"><circle cx="16" cy="16" r="13"/><circle cx="16" cy="16" r="7"/><circle cx="16" cy="16" r="2"/><path d="M4 9c3-5 8-7 13-7"/></svg></div>
  <div class="benefit-icon" style="left:600px;top:724px"><svg width="34" height="26" viewBox="0 0 34 26" fill="none" stroke="#fff" stroke-width="2"><rect x="2" y="4" width="19" height="14"/><path d="M21 8h6l5 5v5H21Z"/><circle cx="8" cy="21" r="3"/><circle cx="26" cy="21" r="3"/></svg></div>

  <div class="benefit-label center" style="left:600px;top:214px"><b>Charing time</b>7-10hours</div>
  <div class="benefit-label right" style="right:791px;top:331px"><b>Dimension</b>3500*1360*1680mm</div>
  <div class="benefit-label" style="left:800px;top:331px"><b>Color</b>White</div>
  <div class="benefit-label right" style="right:855px;top:440px"><b>Battery</b>60v50ah</div>
  <div class="benefit-label" style="left:857px;top:440px"><b>Drive way</b>RWD</div>
  <div class="benefit-label right" style="right:855px;top:558px"><b>Motor</b>1500w</div>
  <div class="benefit-label" style="left:857px;top:558px"><b>Tyre</b>145vacuum</div>
  <div class="benefit-label right" style="right:788px;top:658px"><b>Max speed</b>35-45km/h</div>
  <div class="benefit-label" style="left:792px;top:658px"><b>Brake</b>Four-wheel disc</div>
  <div class="benefit-label center" style="left:600px;top:772px"><b>Controller</b>24tubes</div>
</section>

<section class="testimonials">
  <h2 class="section-title">Testimonials</h2>

  <article class="quote-card" style="left:129px;top:190px">
    <div class="avatar" role="img" aria-label="Customer portrait"></div>
    <div class="stars"><svg viewBox="0 0 12 12"><path d="M6 1l1.5 3.2 3.5.4-2.6 2.4.7 3.5L6 8.8 2.9 10.5l.7-3.5L1 4.6l3.5-.4Z" fill="none" stroke="#82ad21"/></svg><svg viewBox="0 0 12 12"><path d="M6 1l1.5 3.2 3.5.4-2.6 2.4.7 3.5L6 8.8 2.9 10.5l.7-3.5L1 4.6l3.5-.4Z" fill="none" stroke="#82ad21"/></svg><svg viewBox="0 0 12 12"><path d="M6 1l1.5 3.2 3.5.4-2.6 2.4.7 3.5L6 8.8 2.9 10.5l.7-3.5L1 4.6l3.5-.4Z" fill="none" stroke="#82ad21"/></svg><svg viewBox="0 0 12 12"><path d="M6 1l1.5 3.2 3.5.4-2.6 2.4.7 3.5L6 8.8 2.9 10.5l.7-3.5L1 4.6l3.5-.4Z" fill="none" stroke="#82ad21"/></svg><svg viewBox="0 0 12 12"><path d="M6 1l1.5 3.2 3.5.4-2.6 2.4.7 3.5L6 8.8 2.9 10.5l.7-3.5L1 4.6l3.5-.4Z" fill="none" stroke="#82ad21"/></svg></div>
    <div class="quote-name">Dana Whitfield</div>
    <p class="quote-text">Lorem ipsum dolor sit amet, consectetur adipiscing elit, sed do eiusmod tempor incididunt ut labore et dolore magna aliqua. Ut enim ad minim veniam, quis nostrud exercitation ullamco laboris nisi ut aliquip ex ea commodo consequat. Duis aute irure dolor in reprehenderit in voluptate velit esse cillum dolore</p>
  </article>

  <article class="quote-card" style="left:451px;top:149px">
    <div class="avatar" role="img" aria-label="Customer portrait"></div>
    <div class="stars"><svg viewBox="0 0 12 12"><path d="M6 1l1.5 3.2 3.5.4-2.6 2.4.7 3.5L6 8.8 2.9 10.5l.7-3.5L1 4.6l3.5-.4Z" fill="none" stroke="#82ad21"/></svg><svg viewBox="0 0 12 12"><path d="M6 1l1.5 3.2 3.5.4-2.6 2.4.7 3.5L6 8.8 2.9 10.5l.7-3.5L1 4.6l3.5-.4Z" fill="none" stroke="#82ad21"/></svg><svg viewBox="0 0 12 12"><path d="M6 1l1.5 3.2 3.5.4-2.6 2.4.7 3.5L6 8.8 2.9 10.5l.7-3.5L1 4.6l3.5-.4Z" fill="none" stroke="#82ad21"/></svg><svg viewBox="0 0 12 12"><path d="M6 1l1.5 3.2 3.5.4-2.6 2.4.7 3.5L6 8.8 2.9 10.5l.7-3.5L1 4.6l3.5-.4Z" fill="none" stroke="#82ad21"/></svg><svg viewBox="0 0 12 12"><path d="M6 1l1.5 3.2 3.5.4-2.6 2.4.7 3.5L6 8.8 2.9 10.5l.7-3.5L1 4.6l3.5-.4Z" fill="none" stroke="#82ad21"/></svg></div>
    <div class="quote-name">Dana Whitfield</div>
    <p class="quote-text">Lorem ipsum dolor sit amet, consectetur adipiscing elit, sed do eiusmod tempor incididunt ut labore et dolore magna aliqua. Ut enim ad minim veniam, quis nostrud exercitation ullamco laboris nisi ut aliquip ex ea commodo consequat. Duis aute irure dolor in reprehenderit in voluptate velit esse cillum dolore</p>
  </article>

  <article class="quote-card" style="left:772px;top:190px">
    <div class="avatar" role="img" aria-label="Customer portrait"></div>
    <div class="stars"><svg viewBox="0 0 12 12"><path d="M6 1l1.5 3.2 3.5.4-2.6 2.4.7 3.5L6 8.8 2.9 10.5l.7-3.5L1 4.6l3.5-.4Z" fill="none" stroke="#82ad21"/></svg><svg viewBox="0 0 12 12"><path d="M6 1l1.5 3.2 3.5.4-2.6 2.4.7 3.5L6 8.8 2.9 10.5l.7-3.5L1 4.6l3.5-.4Z" fill="none" stroke="#82ad21"/></svg><svg viewBox="0 0 12 12"><path d="M6 1l1.5 3.2 3.5.4-2.6 2.4.7 3.5L6 8.8 2.9 10.5l.7-3.5L1 4.6l3.5-.4Z" fill="none" stroke="#82ad21"/></svg><svg viewBox="0 0 12 12"><path d="M6 1l1.5 3.2 3.5.4-2.6 2.4.7 3.5L6 8.8 2.9 10.5l.7-3.5L1 4.6l3.5-.4Z" fill="none" stroke="#82ad21"/></svg><svg viewBox="0 0 12 12"><path d="M6 1l1.5 3.2 3.5.4-2.6 2.4.7 3.5L6 8.8 2.9 10.5l.7-3.5L1 4.6l3.5-.4Z" fill="none" stroke="#82ad21"/></svg></div>
    <div class="quote-name">Dana Whitfield</div>
    <p class="quote-text">Lorem ipsum dolor sit amet, consectetur adipiscing elit, sed do eiusmod tempor incididunt ut labore et dolore magna aliqua. Ut enim ad minim veniam, quis nostrud exercitation ullamco laboris nisi ut aliquip ex ea commodo consequat. Duis aute irure dolor in reprehenderit in voluptate velit esse cillum dolore</p>
  </article>

  <div class="slider-arrows">
    <span><svg width="22" height="12" viewBox="0 0 22 12"><path d="M21 6H3M7 1 2 6l5 5" stroke="#111" stroke-width="2.4" fill="none"/></svg></span>
    <span><svg width="22" height="12" viewBox="0 0 22 12"><path d="M1 6h18M15 1l5 5-5 5" stroke="#111" stroke-width="2.4" fill="none"/></svg></span>
  </div>
</section>

<footer class="site-footer">
  <div class="brand">
    <div class="brand-name">PLUM WHEELS</div>
    <div class="brand-tag">Cruise along on a plum wheel.</div>
  </div>
  <ul class="footer-links">
    <li>Home</li><li>About</li><li>Product</li><li>Blog</li><li>Contact Us</li>
  </ul>
  <ul class="footer-contact">
    <li><svg width="12" height="12" viewBox="0 0 12 12"><path d="M2 1h3l1 3-2 1a7 7 0 0 0 3 3l1-2 3 1v3c-6 0-10-4-9-9Z" fill="#333"/></svg>+1 888-555-0142</li>
    <li><svg width="12" height="10" viewBox="0 0 12 10"><rect width="12" height="10" fill="#333"/><path d="M0 1l6 4 6-4" stroke="#fff" fill="none"/></svg>info@plumwheelsco.ca</li>
    <li class="addr"><svg width="10" height="13" viewBox="0 0 10 13" style="top:7px"><path d="M5 0a5 5 0 0 1 5 5c0 3-5 8-5 8S0 8 0 5a5 5 0 0 1 5-5Z" fill="#333"/><circle cx="5" cy="5" r="2" fill="#fff"/></svg>1900, Lorem ipsum dolor sit amet,<br>consectetur adipiscing elit, sed</li>
  </ul>
  <div class="subscribe">
    <h3>SUBSCRIBE</h3>
    <p>Lorem ipsum dolor sit amet, consectetur</p>
    <div class="subscribe-form"><span>Email</span><b>Subscribe</b></div>
  </div>
  <p class="copyright">Copyrights © 2022 All Rights Reserved</p>
  <div class="social" aria-label="Social links"><span></span><span></span><span></span><span></span></div>
</footer>

</body>
</html>
```